Business Card for Field Bloom-Eco Friendly Organic Clothing Brand

We are looking for an amazing business card for our eco friendly, organic clothing brand. We are thinking maybe a business card with a peel off sticker on the back, since our hanging clothing tag is a peel off sticker on the back. I will attach our hang tag so we can make sure we stay in line with our design. I've also attached a bag we are doing because I do like the scattered emblem look as well.

```html
<!DOCTYPE html>
<html lang="en">
<head>
<meta charset="utf-8">
<title>Field Bloom – Business Card</title>
<link href="https://fonts.googleapis.com/css2?family=Arimo:wght@400;700&display=swap" rel="stylesheet">
<style>
  :root {
    --backdrop: #e7e4df;
    --card-white: #ffffff;
    --card-shade: #e4e4e4;
    --ink: #1c1c1c;
    --ink-soft: #555555;
    --gold: #c9a642;
    --gold-deep: #9c7a22;
    --black: #0d0d0d;
    --black-soft: #2a2a2a;
  }
  * { margin: 0; padding: 0; box-sizing: border-box; }
  html, body {
    width: 1200px; height: 950px; overflow: hidden;
    background: var(--backdrop);
    font-family: "Arimo", Arial, sans-serif;
  }
  .canvas { position: relative; width: 1200px; height: 950px; }

  .card {
    position: absolute; left: 250px; width: 700px; height: 400px;
    border-radius: 6px; overflow: hidden;
    box-shadow: 0 8px 24px rgba(0,0,0,.18);
  }

  /* Back */
  .card-back { top: 55px; background: linear-gradient(160deg, var(--black-soft), var(--black) 60%); }
  .back-pattern {
    position: absolute; inset: 0;
    background: linear-gradient(140deg, rgba(255,255,255,.05), rgba(255,255,255,0) 55%, rgba(255,255,255,.04));
  }
  .back-tag {
    position: absolute; left: 150px; top: 120px; width: 400px; height: 130px;
    border: 3px solid var(--gold); border-radius: 14px;
    background: var(--black);
    padding: 14px;
  }
  .back-tag .tag-icons {
    width: 100%; height: 100%; border-radius: 8px;
    background: linear-gradient(90deg, #2b2412, #3a3016 50%, #2b2412);
  }
  .back-web {
    position: absolute; right: 36px; bottom: 26px;
    color: #8a8a8a; font-size: 17px; letter-spacing: 2px;
  }

  /* Front */
  .card-front { top: 495px; background: linear-gradient(180deg, var(--card-white) 55%, var(--card-shade)); }
  .brand {
    position: absolute; left: 0; right: 0; top: 70px;
    display: flex; justify-content: center; align-items: center; gap: 14px;
  }
  .brand-square { width: 22px; height: 22px; background: var(--gold-deep); }
  .brand-name { font-size: 38px; font-weight: 700; color: var(--gold-deep); }

  .rule { position: absolute; height: 1px; background: var(--ink); }
  .rule-top { left: 40px; top: 160px; width: 440px; }
  .rule-bottom { left: 260px; top: 262px; width: 400px; }

  .person { position: absolute; left: 40px; top: 172px; color: var(--ink); }
  .person-name { font-size: 22px; font-weight: 700; }
  .person-role { font-size: 16px; margin-top: 2px; }
  .person-address { font-size: 16px; color: var(--ink-soft); margin-top: 8px; line-height: 1.3; }

  .contact { position: absolute; right: 36px; top: 274px; list-style: none; }
  .contact li {
    display: flex; justify-content: flex-end; align-items: center; gap: 10px;
    font-size: 17px; color: var(--ink-soft); line-height: 26px;
  }
  .contact svg { width: 16px; height: 16px; fill: var(--gold); }
</style>
</head>
<body>
<main class="canvas">

  <section class="card card-back" aria-label="Card back">
    <div class="back-pattern" role="img" aria-label="Faint scattered words and emblems pattern"></div>
    <div class="back-tag">
      <div class="tag-icons" role="img" aria-label="Gold hang-tag icons: meditating figure, heart, peace and hand signs"></div>
    </div>
    <p class="back-web">fieldbloom.com</p>
  </section>

  <section class="card card-front" aria-label="Card front">
    <div class="brand">
      <span class="brand-square"></span>
      <span class="brand-name">Field Bloom</span>
    </div>

    <div class="rule rule-top"></div>

    <div class="person">
      <p class="person-name">Mara Quill</p>
      <p class="person-role">President</p>
      <p class="person-address">4127 Alder Crest Lane<br>Cedar Hollow, NY 12045</p>
    </div>

    <div class="rule rule-bottom"></div>

    <ul class="contact">
      <li>555 0142 7781
        <svg viewBox="0 0 16 16"><path d="M1 5c0-2 3-3 7-3s7 1 7 3v1h-4V5H5v1H1zM3 7h10l1 7H2z"/></svg></li>
      <li>555 0193 4406
        <svg viewBox="0 0 16 16"><path d="M4 1h8v14H4zM5 2.5v9.5h6V2.5z"/></svg></li>
      <li>555 0167 2259
        <svg viewBox="0 0 16 16"><path d="M4 1h7v4H4zM1 6h14v7H1zM4 11h8v4H4z"/></svg></li>
      <li>hello@fieldbloom.com
        <svg viewBox="0 0 16 16"><path d="M1 3h14v10H1zM2 4l6 5 6-5z"/></svg></li>
    </ul>
  </section>

</main>
</body>
</html>
```